Modern Business Card for Larkwell 2018

Our company assumes the best about people. We are creating an online community of entrepreneurs and business leaders who struggle with marketing their business online.

This business card should POP! We recently got a new logo and are launching a new website next month, so our business cards should make a statement that feels:
-Fresh
-Smart
-Trustworthy
-Fun

Target Market(s)

small business owners, entrepreneurs

Industry/Entity Type

Digital Marketing

Contact Information for Business Card

Dimensions: 3.5" x 2"

Font styles to use
Sans Serif

Colors
f37122
ffffff

Requirements
Must have
• We need a business card with a modern, bold design. We will use one side of the card as a lead-generation offer, so text on one side will need to fit up to 140 characters. The business card should stick to our core colors (orange, black, and white).
Nice to have
• We think a vertical "portrait" design could be interesting.
Should not have
• Should not look like a traditional business card. The round icon should stand out from a distance.

```html
<!DOCTYPE html>
<html lang="en">
<head>
<meta charset="utf-8">
<title>Larkwell Business Card</title>
<link rel="stylesheet" href="https://fonts.googleapis.com/css2?family=Allura&family=Permanent+Marker&family=Roboto+Condensed:wght@400&family=Roboto:wght@400;500;700;900&display=swap">
<style>
  :root {
    --orange: #f37122;
    --orange-deep: #e8631f;
    --black: #1b1b1b;
    --white: #ffffff;
    --paper: #f4f4f4;
    --ink: #222222;
    --rule: #8a8a8a;
    --backdrop: #e4e4e4;
  }
  * { box-sizing: border-box; margin: 0; padding: 0; }
  html, body { width: 1200px; height: 960px; overflow: hidden; }
  body { background: var(--backdrop); position: relative; font-family: "Roboto", sans-serif; }

  .card { position: absolute; top: 180px; width: 343px; height: 600px; overflow: hidden; }

  /* Front: personal side */
  .card--front { left: 249px; background: var(--paper); }
  .front__tab { position: absolute; left: 248px; top: 0; width: 50px; height: 116px;
    background: var(--orange-deep); border-radius: 0 0 25px 25px; }
  .front__details { position: absolute; left: 0; right: 0; top: 428px; text-align: center; }
  .front__name { font-family: "Allura", cursive; color: var(--orange-deep); font-size: 58px;
    line-height: 1; margin-left: 40px; }
  .front__title { font-weight: 500; font-size: 16px; color: var(--ink); margin-top: 2px; letter-spacing: 0.2px; }
  .front__email { font-size: 14px; color: var(--ink); margin-top: 8px; }

  /* Back: lead-generation side */
  .card--back { left: 608px; background: var(--black); }
  .back__band { position: absolute; left: 0; right: 0; top: 266px; height: 275px; background: var(--orange-deep); }
  .back__brand { position: absolute; left: 0; right: 0; top: 28px; text-align: center; color: var(--white); }
  .brand__dot { width: 44px; height: 44px; border-radius: 50%; background: var(--orange-deep); margin: 0 auto 14px; }
  .brand__name { font-weight: 700; font-size: 45px; letter-spacing: 1px; line-height: 1; }
  .brand__tagline { font-family: "Permanent Marker", cursive; font-size: 14px; letter-spacing: 0.8px; margin-top: 6px; }
  .back__notes { position: absolute; left: 24px; top: 181px; width: 292px; height: 162px;
    background: var(--paper); border-radius: 14px; padding: 43px 20px 0; }
  .notes__line { height: 2px; background: var(--rule); margin-bottom: 37px; }
  .back__pitch { position: absolute; left: 0; right: 0; top: 380px; text-align: center; color: var(--white); }
  .pitch__headline { font-weight: 500; font-size: 23px; line-height: 28px; letter-spacing: 0.2px; }
  .pitch__offer { font-family: "Roboto Condensed", sans-serif; font-size: 15px; line-height: 20px; margin-top: 14px; }
  .back__url { position: absolute; left: 0; right: 0; bottom: 0; height: 59px; line-height: 59px;
    text-align: center; color: var(--white); font-weight: 700; font-size: 22px; }
</style>
</head>
<body>
  <section class="card card--front" aria-label="Business card front">
    <div class="front__tab"></div>
    <div class="front__details">
      <p class="front__name">Dana Whitlow</p>
      <p class="front__title">STORY MARKETING COACH</p>
      <p class="front__email">dana@larkwellnow.com</p>
    </div>
  </section>

  <section class="card card--back" aria-label="Business card back">
    <div class="back__band"></div>
    <div class="back__brand">
      <div class="brand__dot"></div>
      <p class="brand__name">LARKWELL</p>
      <p class="brand__tagline">TELL STORIES THAT INSPIRE ACTION</p>
    </div>
    <div class="back__notes">
      <div class="notes__line"></div>
      <div class="notes__line"></div>
      <div class="notes__line"></div>
    </div>
    <div class="back__pitch">
      <p class="pitch__headline">REACH MORE PEOPLE.<br>MAKE MORE MONEY.<br>CREATE MORE IMPACT.</p>
      <p class="pitch__offer">Get your free Larkwell, Starter Package and our<br>marketing guide today at</p>
    </div>
    <p class="back__url">Larkwellnow.com/start</p>
  </section>
</body>
</html>
```